Business card design Needed for new logo / Construction business, home extensions and new builds

We need a business card design using our new logo files which i will attach to this project :)

We are a small construction business specialising in home extensions, new builds and property development. We are very ambitious and would appreciate professional and elegant designs for our new business card.

Very serious about using the services on MakerQuarry and recently acquired our new logo from here :)

Please get involved, i will feedback when i can as i am very busy but can respond daily, thanks

Target Market(s)

People that want to build onto their houses, new building developments or adding too their existing property

Industry/Entity Type

Construction

Contact Information for Business Card

Renwick Tolliver Construction, Lionel Ashby (Managing Director), Tel 07822254961, email - info@renwick-tolliver, www.renwick-tolliver.co.uk

Colors

Designer to choose colors to be used in the design.

Requirements
Must have
• I like a deep grey on the back please. A lot of you have provided black from and back, try mixing things up a little. The black looks cool 😎 Thanks

```html
<!DOCTYPE html>
<html lang="en">
<head>
<meta charset="utf-8">
<title>Renwick Tolliver Construction – Business Card</title>
<link rel="stylesheet" href="https://fonts.googleapis.com/css2?family=Cinzel:wght@500&family=EB+Garamond:wght@400;500&display=swap">
<style>
  :root {
    --backdrop: #2b2b2d;
    --card-black: #161616;
    --card-grey: #1f1f20;
    --silver: #d9dadc;
    --silver-dark: #8d8f93;
    --gold: #d9a521;
    --text-light: #e6e6e6;
    --divider: #3a3a3c;
  }
  * { margin: 0; padding: 0; box-sizing: border-box; }
  html, body { width: 1200px; height: 689px; overflow: hidden; }
  body {
    background: var(--backdrop);
    display: flex;
    align-items: center;
    justify-content: center;
    gap: 48px;
    font-family: "EB Garamond", Georgia, serif;
  }
  .card {
    position: relative;
    width: 540px;
    height: 310px;
    border-radius: 18px;
    overflow: hidden;
    box-shadow: 0 18px 40px rgba(0,0,0,.55);
  }

  /* Back (pattern side) */
  .card-back { background: var(--card-black); }
  .back-pattern {
    position: absolute; inset: 0;
    background: linear-gradient(135deg, #101010 0%, #1c1c1c 45%, #3a3a3c 100%);
  }
  .back-brand {
    position: absolute; inset: 0;
    display: flex; flex-direction: column; align-items: center; justify-content: center;
  }

  .brand-mark {
    display: flex; align-items: center; gap: 12px;
    font-family: "Cinzel", serif;
    font-weight: 500;
    color: var(--silver);
    letter-spacing: .06em;
  }
  .brand-square { width: 16px; height: 16px; background: var(--gold); }
  .brand-sub {
    display: flex; align-items: center; gap: 10px;
    font-family: "Cinzel", serif; font-weight: 500;
    color: var(--gold); letter-spacing: .12em;
  }
  .brand-sub::before, .brand-sub::after {
    content: ""; width: 28px; height: 2px; background: var(--gold);
  }
  .card-back .brand-mark { font-size: 27px; }
  .card-back .brand-sub { font-size: 17px; margin-top: 4px; }

  /* Front (contact side) */
  .card-front { background: var(--card-grey); }
  .front-logo {
    position: absolute; left: 0; top: 0; width: 290px; height: 272px;
    display: flex; flex-direction: column; align-items: center; justify-content: center;
  }
  .card-front .brand-mark { font-size: 22px; }
  .card-front .brand-sub { font-size: 14px; margin-top: 4px; }
  .front-divider {
    position: absolute; left: 290px; top: 40px; width: 1px; height: 190px;
    background: var(--divider);
  }
  .contact {
    position: absolute; left: 314px; top: 46px; right: 16px;
    color: var(--text-light);
  }
  .contact-name {
    font-family: "Cinzel", serif; font-weight: 500;
    font-size: 19px; letter-spacing: .04em; color: var(--silver);
  }
  .contact-role { font-size: 15px; color: var(--gold); margin-bottom: 14px; }
  .contact-line {
    display: flex; align-items: center; gap: 8px;
    font-size: 13.5px; line-height: 1.5;
  }
  .contact-line svg { width: 12px; height: 12px; flex: none; fill: var(--silver); }
  .contact-address { margin-top: 14px; font-size: 13.5px; line-height: 1.35; }

  .silver-band {
    position: absolute; left: 0; right: 0; bottom: 0; height: 38px;
    background: linear-gradient(180deg, #2a2a2b 0%, var(--silver-dark) 30%, var(--silver) 55%, #6e7074 100%);
    clip-path: polygon(0 80%, 86% 20%, 92% 0, 100% 0, 100% 100%, 0 100%);
  }
  .band-square {
    position: absolute; right: 22px; bottom: 18px; width: 8px; height: 8px; background: var(--gold);
  }
</style>
</head>
<body>

  <section class="card card-back" aria-label="Card back">
    <div class="back-pattern" role="img" aria-label="Tonal repeating brand pattern across the card"></div>
    <div class="back-brand">
      <div class="brand-mark"><span class="brand-square"></span>Renwick Tolliver</div>
      <div class="brand-sub">Construction</div>
    </div>
  </section>

  <section class="card card-front" aria-label="Card front">
    <div class="front-logo">
      <div class="brand-mark"><span class="brand-square"></span>Renwick Tolliver</div>
      <div class="brand-sub">Construction</div>
    </div>
    <div class="front-divider"></div>
    <div class="contact">
      <div class="contact-name">Lionel Ashby</div>
      <div class="contact-role">Managing Director</div>
      <div class="contact-line">
        <svg viewBox="0 0 24 24"><path d="M6.6 10.8a15 15 0 0 0 6.6 6.6l2.2-2.2a1 1 0 0 1 1-.25 11.4 11.4 0 0 0 3.6.57 1 1 0 0 1 1 1V20a1 1 0 0 1-1 1A17 17 0 0 1 3 4a1 1 0 0 1 1-1h3.5a1 1 0 0 1 1 1c0 1.25.2 2.45.57 3.57a1 1 0 0 1-.25 1z"/></svg>
        07822254961
      </div>
      <div class="contact-line">
        <svg viewBox="0 0 24 24"><path d="M2 5h20v14H2zm2 2v.5l8 5 8-5V7zm0 3v7h16v-7l-8 5z"/></svg>
        info@renwick-tolliver
      </div>
      <div class="contact-line">
        <svg viewBox="0 0 24 24"><path d="M12 2a10 10 0 1 0 0 20 10 10 0 0 0 0-20zm-1 2.1V8H7.3A8 8 0 0 1 11 4.1zm2 0A8 8 0 0 1 16.7 8H13zM4.6 10H11v4H4.6a8 8 0 0 1 0-4zM13 10h6.4a8 8 0 0 1 0 4H13zm-5.7 6H11v3.9A8 8 0 0 1 7.3 16zm5.7 0h3.7a8 8 0 0 1-3.7 3.9z"/></svg>
        www.renwick-tolliver.co.uk
      </div>
      <div class="contact-address">68, Harrow Mill Lane<br>30917, Northbridge</div>
    </div>
    <div class="silver-band"></div>
    <span class="band-square"></span>
  </section>

</body>
</html>
```